Corporate Design für Hotel/Restaurant
Zielgruppe
Unsere Kundschaft ist sehr breit gestreut. Unser CI sollte entsprechend die Ü60 jährigen, wie auch die ca. 30+ jährigen Kleinstädter ansprechen.
Aufgabenstellung
Es handelt sich um einen Familienbetrieb in zweiter Generation, der trotz altem deutschen Namen „Hotel-Restaurant zum Brunnenhof“ eine klare asiatische Ausrichtung, sowohl vom Interieur, wie auch vom Speisenangebot hat.
Der rote Familienstempel soll sich auch weiterhin im Design finden (muss allerdings nicht unbedingt rot sein).
Ebenso möchten wir das Bild der Mutter aus Ihrer Jungend weiter aufgreifen.
Wir könnten uns ein ähnliches Bild auf den Tischen vorstellen, wie im Anhang zu sehen.
Wir möchten neue Speisekarten für die Abend- und Mittagskarte entwerfen lassen, die gerne mit Skizzen von koreanischem Streetfood untermalt werden sollen.
Wir stellen uns eine Bindung der Speisekarte auf einem Klemmbrett oder durch eine Holzleiste an der Seite (wie bei einem Buch) vor. Hierfür benötigen wir auch entsprechende Papiervorschläge. Wir möchten keine laminierte Speisekarte, eventuell, aber gewachstes, robustes Papier.
Auch bedruckte Tischsets könnten wir uns vorstellen, sowie im weiteren Schritt Essstäbchen mit Gravur oder Druck. Desweiteren wären Papierservietten wünschenswert.
Generell muss ein Spagat zwischen Deutsch und Asiatisch hergestellt werden.
Unsere Typografie ist festgesetzt auf SAUNA SMALL CAPS
wir interessieren uns weiterhin für Poloshirt, Sweater oder Schürzen mit dem neuen CI

```html
<!DOCTYPE html>
<html lang="de">
<head>
<meta charset="utf-8">
<title>Hotel-Restaurant zum Brunnenhof – Visitenkarten</title>
<link href="https://fonts.googleapis.com/css2?family=Alegreya+Sans+SC:wght@400;500&display=swap" rel="stylesheet">
<style>
  :root {
    --backdrop: #b3a5a2;
    --paper: #e9e5d8;
    --ink: #1f1d1c;
    --accent-red: #c3172b;
    --accent-red-soft: #d23a48;
    --paper-on-red: #eee6d8;
  }
  * { box-sizing: border-box; margin: 0; padding: 0; }
  html, body { width: 857px; height: 1200px; overflow: hidden; }
  body {
    background: var(--backdrop);
    font-family: "Alegreya Sans SC", "Trebuchet MS", sans-serif;
    color: var(--ink);
    position: relative;
  }
  .card {
    position: absolute;
    left: 108px;
    width: 640px;
    height: 366px;
    background: var(--paper);
    box-shadow: 0 6px 18px rgba(40, 25, 25, 0.25);
    overflow: hidden;
  }
  .card--front { top: 150px; }
  .card--back { top: 640px; }

  .artwork-row { position: absolute; display: flex; }
  .artwork {
    border-radius: 50%;
    background: radial-gradient(ellipse at center, var(--accent-red-soft) 0%, var(--accent-red) 75%);
  }
  .card--front .artwork-row { top: 46px; left: 226px; gap: 28px; }
  .card--front .artwork { width: 80px; height: 102px; }
  .card--back .artwork-row { top: 76px; left: 60px; gap: 16px; }
  .card--back .artwork { width: 62px; height: 80px; }

  .brand-name {
    font-weight: 400;
    text-transform: uppercase;
    line-height: 0.95;
    letter-spacing: 0.5px;
    position: absolute;
  }
  .card--front .brand-name {
    top: 182px; left: 0; width: 100%;
    text-align: center;
    font-size: 46px;
  }
  .card--back .brand-name {
    top: 50px; left: 290px;
    font-size: 27px;
  }

  .contact-band {
    position: absolute;
    top: 176px; left: 0;
    width: 640px; height: 110px;
  }
  .phone {
    position: absolute;
    top: 206px; left: 40px;
    font-size: 44px;
    letter-spacing: 2px;
    color: var(--paper-on-red);
  }
  .hours {
    position: absolute;
    top: 194px; left: 392px;
    font-size: 17px;
    line-height: 1.15;
    color: var(--paper-on-red);
  }
  .address {
    position: absolute;
    top: 296px; left: 150px;
    font-size: 19px;
    line-height: 1.1;
  }
</style>
</head>
<body>

<section class="card card--front">
  <div class="artwork-row">
    <div class="artwork" role="img" aria-label="Rote Stempelillustration: Porträt der Mutter in jungen Jahren"></div>
    <div class="artwork" role="img" aria-label="Rote Stempelillustration: koreanischer Pavillon am Wasser"></div>
  </div>
  <h1 class="brand-name">Hotel-Restaurant<br>zum Brunnenhof</h1>
</section>

<section class="card card--back">
  <div class="artwork-row">
    <div class="artwork" role="img" aria-label="Rote Stempelillustration: Porträt der Mutter in jungen Jahren"></div>
    <div class="artwork" role="img" aria-label="Rote Stempelillustration: koreanischer Pavillon am Wasser"></div>
  </div>
  <h2 class="brand-name">Hotel-Restaurant<br>zum Brunnenhof</h2>

  <svg class="contact-band" viewBox="0 0 640 110" preserveAspectRatio="none" aria-hidden="true">
    <polygon fill="var(--accent-red)" points="0,6 40,2 90,7 150,1 220,5 300,0 380,6 460,2 540,6 600,1 640,4 640,104 590,109 520,103 440,108 360,103 280,109 200,104 120,109 60,104 0,108"/>
  </svg>
  <p class="phone">05231 / 772-0</p>
  <p class="hours">Rezeption /<br>täglich besetzt von:<br>06:00 – 22:00 Uhr</p>

  <p class="address">Lindenallee 14,<br>31600 Waldstedt</p>
</section>

</body>
</html>
```